Migration and redesign of existing website to WordPress using DIVI 3

I. TASK OBJECTIVE:
- Redesign our existing website www.kelvaleheelcare.com.au with a fresh new look and migrate to new Wordpress site based on DIVI3 theme. The site will contain the same basic functionality as the existing site (with some small changes).

II. STYLE/ DESIGN ASPECT:
As an example of a site that I like the look of, see https://pebblequarn.com/. I like the use of shadows, and this would go well with the little animations you can do with Divi (e.g. when hovering over pics).

1. What I am looking for is a design which has lots of white space, is modern and friendly looking (but still not too cute or frivolous, as we are a medical practice)
2. DESIGN that is NOT TOO rectangular or blocky.
3. Please take into consideration our Users are Older market, so any icons or navigation features need to be very easy to understand and not too small.
4. Must be easy to navigate
5. We are are happy to go with a new colour scheme, and are working on some ideas for this, but happy to take suggestions.

III. SPECIFICATIONS:
1. 5+ Pages (should flow like the current site)
2. Using Wordpress Divi 3 theme.
3. I'd like every page to have a "book now" button and a contact form in a sidebar so that users can click the button or fill in the contact form without scrolling at all. EXCEPT ON THE HOME PAGE, where there should still be a book now button (maybe on the top right in the header of all pages?), and maybe a contact us button which scrolls down to the contact area at the bottom of the HOME page. I don't think a side bar is necessarily required on the home page, but if you think it makes sense from a design perspective please let me know.
4. AT THE BOTTOM OF THE PAGE, just above the FOOTER, I'd like a row of trust logos for various organisations that we are affiliated with. (A list of this company will be provided later but you could temporarily use placeholders)

Once we have a structure in place, we can migrate most of the content. Please let me know if I'm not being clear or you need further information.

Podiatry Customers and Referrors

Health Care

5+ page

• Simple to navigate.
• Contact/booking details on most if not all pages - please see specification above
• Section for Trusted Affiliates above the footer
• Wordpress using Divi3 Theme
• Not too busy with the design. Plenty of white space or light background.
• Should not be complicated to navigate.
• TOO rectangular or blocky designs

```html
<!DOCTYPE html>
<html lang="en">
<head>
<meta charset="utf-8">
<title>Kelvale Heel Care Clinic</title>
<link rel="stylesheet" href="https://fonts.googleapis.com/css2?family=Open+Sans:wght@400;600;700&family=Oswald:wght@500&display=swap">
<style>
:root{
  --teal:#0e6b6c;
  --teal-deep:#0a5758;
  --button:#3898b2;
  --ink:#2b2b2b;
  --body:#6d6d6d;
  --line:#d9d9d9;
  --grey-band:#f2f2f2;
  --badge:#e4e7e8;
  --footer:#1f1f1f;
  --white:#ffffff;
}
*{margin:0;padding:0;box-sizing:border-box}
html,body{width:1200px;height:3390px;overflow:hidden;background:var(--white)}
body{position:relative;font-family:"Open Sans",Arial,sans-serif;color:var(--ink)}
.abs{position:absolute}
.btn{position:absolute;display:flex;align-items:center;justify-content:center;color:var(--white);background:var(--button);border-radius:20px;font-size:13px}

/* header */
.brand{left:124px;top:16px;display:flex;align-items:center;gap:10px}
.brand-mark{width:34px;height:34px;border-radius:50%;background:var(--teal)}
.brand-name{font-size:17px;font-weight:600;color:var(--teal)}
.contact-top{left:742px;top:30px;display:flex;gap:10px;align-items:flex-start}
.contact-top p{font-size:16px;line-height:19px;color:var(--ink)}
.contact-top p small{font-size:12px}
.appointment{left:976px;top:34px;width:136px;height:36px;background:var(--teal);font-size:16px;font-weight:600;border-radius:18px}
.nav{left:63px;top:106px;width:1076px;height:57px;border:1px solid var(--line);display:flex;align-items:center;justify-content:space-between;padding:0 40px 0 48px}
.nav a{font-size:16px;color:var(--ink);text-decoration:none}
.nav a.current{color:var(--teal)}

/* hero */
.hero{left:0;top:163px;width:1200px;height:527px;background:linear-gradient(120deg,#c7ccd0 0%,#e4e6e8 35%,#d9d4cf 60%,#a9a39e 100%)}
.hero-wave{left:0;top:560px}
.hero-title{right:88px;top:340px;font-family:"Oswald",Arial,sans-serif;font-weight:500;font-size:54px;color:var(--teal);letter-spacing:1px;text-align:right;white-space:nowrap}
.hero-sub{right:88px;top:412px;font-size:24px;color:#3d3d3d;text-align:right;white-space:nowrap}
.slider-arrows{left:1050px;top:492px;display:flex;gap:4px}
.slider-arrows span{width:22px;height:22px;border-radius:50%;background:#8a8a8a;display:block}

/* sections */
h2.sec{position:absolute;font-weight:400;font-size:29px;line-height:38px;color:var(--ink)}
p.copy{position:absolute;font-size:13px;line-height:22px;color:var(--body)}
.photo{position:absolute;border:3px solid var(--white);box-shadow:0 0 0 1px var(--line),0 3px 10px rgba(0,0,0,.12)}

.practice{left:0;top:1141px;width:1200px;height:482px;background:var(--teal)}
.practice h2{position:absolute;top:80px;width:1200px;text-align:center;color:var(--white);font-size:28px;font-weight:400}
.area{position:absolute;top:176px;width:270px;text-align:center;color:var(--white)}
.area svg{display:block;margin:0 auto}
.area h3{font-size:19px;font-weight:400;margin-top:28px}
.area p{font-size:13px;line-height:23px;margin-top:10px}

.team{left:0;top:2084px;width:1200px;height:493px;background:var(--grey-band)}
.team h2{position:absolute;top:75px;width:1200px;text-align:center;font-size:28px;font-weight:400}
.member{position:absolute;top:168px;width:220px;text-align:center}
.avatar{width:138px;height:138px;border-radius:50%;margin:0 auto;border:5px solid var(--white);box-shadow:0 3px 10px rgba(0,0,0,.2)}
.member h3{font-size:15px;font-weight:400;margin-top:26px;line-height:19px}
.member p{font-size:13px;line-height:19px}
.member .social{display:flex;gap:6px;justify-content:center;margin-top:14px}
.member .social span{width:20px;height:20px;border-radius:50%;background:var(--teal)}

.field{position:absolute;border:1px solid var(--line);border-radius:4px;font-size:13px;color:var(--ink);padding:0 12px;display:flex;align-items:center;box-shadow:0 1px 3px rgba(0,0,0,.06)}
.field.tall{align-items:flex-start;padding-top:14px}

/* trusted affiliates */
.affiliates{left:90px;top:2984px;width:1020px;display:flex;justify-content:space-between}
.affiliates span{width:140px;height:40px;border-radius:20px;background:var(--badge)}

/* footer */
.footer{left:0;top:3080px;width:1200px;height:310px;background:var(--footer)}
.footer h4{position:absolute;top:62px;color:var(--white);font-size:15px;font-weight:400}
.footer ul{position:absolute;top:100px;list-style:none}
.footer li{color:var(--white);font-size:12px;line-height:23px}
.footer li.link::before{content:"» ";}
.footer .info li{display:flex;align-items:flex-start;gap:10px;line-height:20px;margin-bottom:8px}
.mail-copy{top:98px;left:642px;width:210px;color:var(--white);font-size:12px;line-height:16px;position:absolute}
.mail-form{left:642px;top:138px;display:flex;position:absolute}
.mail-form span{height:28px;display:flex;align-items:center;font-size:11px}
.mail-input{width:150px;background:var(--white);color:#888;padding-left:8px}
.mail-submit{width:56px;background:var(--button);color:var(--white);justify-content:center}
.follow{left:947px;top:104px;display:flex;gap:14px;position:absolute}
.follow span{width:24px;height:24px;border-radius:4px;background:var(--white)}
.footer-rule{left:90px;top:236px;width:1020px;height:1px;background:#3a3a3a}
.copyright{top:260px;width:1200px;text-align:center;color:var(--white);font-size:12px}
</style>
</head>
<body>

<!-- Header -->
<div class="abs brand"><span class="brand-mark"></span><span class="brand-name">Kelvale Heel Care Clinic</span></div>
<div class="abs contact-top">
  <svg width="16" height="30" viewBox="0 0 16 30"><rect x="1.5" y="1.5" width="13" height="27" rx="3" fill="none" stroke="#0e6b6c" stroke-width="2.5"/><circle cx="8" cy="24" r="1.6" fill="#0e6b6c"/></svg>
  <p>+(08) 5550 4127<br><small>info@kelvaleheelcare.com.au</small></p>
</div>
<div class="btn appointment">Appointment</div>

<nav class="abs nav">
  <a class="current">Home</a><a>Common Problems</a><a>Services</a><a>About Us</a><a>Case Histories</a><a>Helpful Information</a><a>Blog</a><a>Contact</a>
</nav>

<!-- Hero -->
<div class="abs hero" role="img" aria-label="Runner's foot on a treadmill with the bones of the foot highlighted"></div>
<svg class="abs hero-wave" width="1200" height="132" viewBox="0 0 1200 132"><path d="M0 40 C250 150 500 120 760 80 C950 50 1080 40 1200 70 L1200 132 L0 132 Z" fill="#ffffff"/></svg>
<div class="abs hero-title">KELVALE HEEL CARE</div>
<div class="abs hero-sub">Our Kelvale Podiatrists Relieve Foot Pain</div>
<div class="abs slider-arrows"><span></span><span></span></div>

<!-- Intro -->
<h2 class="sec" style="left:90px;top:786px;width:480px">Let Our Kelvale Podiatrists Relieve Your Foot and Ankle Pain</h2>
<p class="copy" style="left:90px;top:874px;width:490px">Whether you are an office worker, pensioner, or professional athlete, nearly all people will experience problems in their feet and ankles at some point in their lives. Unfortunately, a problem in the foot can affect the whole body, causing an infection to spread, deformities in the foot, and pain to travel upward into the leg. It doesn't take long before a foot injury may cause wide-ranging consequences, including lost mobility, a drain on your finances, and a decline</p>
<div class="btn" style="left:90px;top:1024px;width:106px;height:36px">Read More</div>
<div class="photo" role="img" aria-label="Podiatrist examining a patient's foot, video still" style="left:635px;top:791px;width:473px;height:267px;background:linear-gradient(100deg,#c8aa94 0%,#e2cbb8 40%,#3f5f8c 75%,#2c4670 100%)"></div>
<svg class="abs" style="left:843px;top:896px" width="56" height="56" viewBox="0 0 56 56"><circle cx="28" cy="28" r="27" fill="rgba(30,30,30,.65)"/><path d="M22 17 L40 28 L22 39 Z" fill="#fff"/></svg>

<!-- Practice Areas -->
<section class="abs practice">
  <h2>Practice Areas</h2>
  <div class="area" style="left:68px">
    <svg width="112" height="112" viewBox="0 0 112 112"><circle cx="56" cy="56" r="53" fill="none" stroke="#fff" stroke-width="3"/><path d="M44 32 h14 v30 l14 8 v10 H44 Z" fill="#fff"/><path d="M44 44 h14 M44 52 h14" stroke="#0e6b6c" stroke-width="3"/></svg>
    <h3>Common Problems</h3><p>When you suffer from a foot and/or<br>ankle problem, the pain</p>
  </div>
  <div class="area" style="left:335px">
    <svg width="112" height="112" viewBox="0 0 112 112"><circle cx="56" cy="56" r="53" fill="none" stroke="#fff" stroke-width="3"/><path d="M48 30 h14 v36 c8 2 12 6 12 12 H46 c0-8 2-12 2-16 Z" fill="#fff"/><path d="M54 44 h6 M54 52 h6" stroke="#0e6b6c" stroke-width="3"/></svg>
    <h3>Foot &amp; Ankle Surgery</h3><p>When you suffer from a foot and/or<br>ankle problem, the pain and</p>
  </div>
  <div class="area" style="left:597px">
    <svg width="112" height="112" viewBox="0 0 112 112"><circle cx="56" cy="56" r="53" fill="none" stroke="#fff" stroke-width="3"/><rect x="38" y="38" width="36" height="40" rx="3" fill="none" stroke="#fff" stroke-width="4"/><path d="M50 38 v-6 h12 v6" fill="none" stroke="#fff" stroke-width="4"/><path d="M56 48 v20 M46 58 h20" stroke="#fff" stroke-width="5"/></svg>
    <h3>Sport and Dance</h3><p>When you suffer from a foot and/or<br>ankle problem, the pain and</p>
  </div>
  <div class="area" style="left:862px">
    <svg width="112" height="112" viewBox="0 0 112 112"><circle cx="56" cy="56" r="53" fill="none" stroke="#fff" stroke-width="3"/><ellipse cx="56" cy="64" rx="10" ry="18" fill="#fff"/><circle cx="48" cy="38" r="4" fill="#fff"/><circle cx="56" cy="35" r="4" fill="#fff"/><circle cx="64" cy="38" r="3.5" fill="#fff"/><circle cx="42" cy="43" r="3" fill="#fff"/><circle cx="69" cy="43" r="3" fill="#fff"/></svg>
    <h3>All Our Services</h3><p>When you suffer from a foot and/or<br>ankle problem, the pain and</p>
  </div>
</section>

<!-- Track record -->
<div class="photo" role="img" aria-label="Gait analysis screen above a treadmill in the clinic" style="left:90px;top:1716px;width:475px;height:284px;background:linear-gradient(160deg,#5c6670 0%,#8d959c 40%,#d9dcde 70%,#bfc3c6 100%)"></div>
<h2 class="sec" style="left:606px;top:1724px;width:510px">A Proven Track Record of Correcting Foot Pain in Perth Patients</h2>
<p class="copy" style="left:606px;top:1806px;width:510px">At the Kelvale Heel Care Clinic, we know that there are often a variety of causes of foot and ankle pain, and each must be addressed to solve your problem for good. We examine your feet, posture, and gait to identify any biomechanical issues that could be causing your pain, treat ulcerations and foot deformities that prohibit full range of motion, and perform many different surgical techniques to restore your mobility and lifestyle. Call the number on this page today</p>
<div class="btn" style="left:606px;top:1959px;width:106px;height:36px">Read More</div>

<!-- Team -->
<section class="abs team">
  <h2>Meet Our Team</h2>
  <div class="member" style="left:100px">
    <div class="avatar" role="img" aria-label="Portrait of Rena Holt" style="background:linear-gradient(160deg,#e9d7b8,#c9a98c)"></div>
    <h3>Rena Holt</h3><p>Podiatric Surgeon</p>
    <div class="social"><span></span><span></span><span></span><span></span></div>
  </div>
  <div class="member" style="left:360px">
    <div class="avatar" role="img" aria-label="Portrait of Owen Trask" style="background:linear-gradient(160deg,#d8b9a4,#9aa3b3)"></div>
    <h3>Owen Trask</h3><p>Podiatrist</p>
    <div class="social"><span></span><span></span><span></span><span></span></div>
  </div>
  <div class="member" style="left:622px">
    <div class="avatar" role="img" aria-label="Portrait of Lina Perrow" style="background:linear-gradient(160deg,#5a4336,#d6b6a0)"></div>
    <h3>Lina Perrow</h3><p>Podiatrist</p>
    <div class="social"><span></span><span></span><span></span><span></span></div>
  </div>
  <div class="member" style="left:884px">
    <div class="avatar" role="img" aria-label="Portrait of Ada Quenby" style="background:linear-gradient(160deg,#c9a37a,#e3c9b1)"></div>
    <h3>Ada Quenby</h3><p>Podiatrist</p>
    <div class="social"><span></span><span></span><span></span><span></span></div>
  </div>
</section>

<!-- Case histories -->
<h2 class="sec" style="left:90px;top:2676px">Case Histories</h2>
<div class="photo" role="img" aria-label="Ballet dancer's feet in pointe shoes" style="left:90px;top:2735px;width:163px;height:174px;background:linear-gradient(150deg,#a9a9a9 0%,#e7dcd6 55%,#cfc1b9 100%)"></div>
<p class="copy" style="left:267px;top:2740px;width:298px;text-align:justify">It is a long established fact that a reader will be distracted by the readable content of a page when looking at its layout. The point of using Lorem Ipsum is that it has a more-or-less normal distribution of letters, as opposed to using 'Content here, content here', making it look</p>
<p class="abs" style="left:272px;top:2882px;font-size:12px;color:var(--teal)">View More »</p>

<!-- Contact -->
<h2 class="sec" style="left:640px;top:2676px">Contact us</h2>
<div class="field" style="left:640px;top:2739px;width:228px;height:50px">Name</div>
<div class="field" style="left:881px;top:2739px;width:229px;height:50px">Email id</div>
<div class="field" style="left:640px;top:2798px;width:228px;height:50px">Phone</div>
<div class="field" style="left:881px;top:2798px;width:229px;height:50px">Subject</div>
<div class="field tall" style="left:640px;top:2857px;width:470px;height:50px">Message</div>
<div class="btn" style="left:1010px;top:2922px;width:100px;height:36px;font-size:14px">SUBMIT</div>

<!-- Trusted affiliates -->
<div class="abs affiliates" role="img" aria-label="Trusted affiliate badges">
  <span></span><span></span><span></span><span></span><span></span><span></span>
</div>

<!-- Footer -->
<svg class="abs" style="left:0;top:3040px" width="1200" height="42" viewBox="0 0 1200 42"><path d="M0 42 L0 28 C300 0 900 0 1200 28 L1200 42 Z" fill="#1f1f1f"/></svg>
<footer class="abs footer">
  <h4 style="left:90px">Quick links</h4>
  <ul style="left:92px"><li class="link">Testimonials</li><li class="link">Products</li><li class="link">Contact</li><li class="link">About us</li></ul>

  <h4 style="left:332px">Contacts</h4>
  <ul class="info" style="left:332px">
    <li><svg width="12" height="16" viewBox="0 0 12 16"><path d="M6 0 C2.7 0 0 2.6 0 5.8 C0 10 6 16 6 16 S12 10 12 5.8 C12 2.6 9.3 0 6 0 Z" fill="#fff"/><circle cx="6" cy="6" r="2.2" fill="#1f1f1f"/></svg><span>14 Marlow Crescent<br>Kelvale, WA 6999</span></li>
    <li><svg width="12" height="14" viewBox="0 0 12 14"><path d="M2 1 L5 1 L6 4 L4 6 C5 8 6 9 8 10 L10 8 L12 9 L12 12 C12 13 11 14 10 14 C4 13 0 8 0 3 C0 2 1 1 2 1 Z" fill="#fff"/></svg><span>(08) 5550 4127</span></li>
    <li><svg width="14" height="12" viewBox="0 0 14 12"><rect width="14" height="12" rx="1" fill="#fff"/><path d="M1 1 L7 7 L13 1" fill="none" stroke="#1f1f1f" stroke-width="1.5"/></svg><span>info@kelvaleheelcare.com.au</span></li>
  </ul>

  <h4 style="left:642px">Join our mailing list</h4>
  <p class="mail-copy">Your about us information would fit here nicely.</p>
  <div class="mail-form"><span class="mail-input">Email address</span><span class="mail-submit">Submit</span></div>

  <h4 style="left:947px">Follow us out there</h4>
  <div class="follow"><span></span><span></span><span></span><span></span></div>

  <div class="abs footer-rule"></div>
  <p class="abs copyright">Copyright © 2017. All Rights Reserved</p>
</footer>

</body>
</html>
```